BuildLinkHub.com Full Stationery Design

Business Card will have all info on it. Letterhead will not have name, title or mobile number. Keep general feeling very clean, using colors from the logo as accents.
Name:Dale Marchetti
Title:President
Phone: 1-800-555-0142
Cell: 306-555-0187
email: dale@buildlinkhub.example
website: www.buildlinkhub.example
Address:
PO Box 947
Ashvale, MB
S0J2T0

Target Market(s)

Construction Business owners

Industry/Entity Type

Business

Contact Information for Business Card

Name:Dale Marchetti
Title:President
Phone: 1-800-555-0142
Cell: 306-555-0187
Address:
PO Box 947
Ashvale, MB
S0J2T0

Font styles to use
Sans Serif

Requirements
Must have
• Clean look
Should not have
• Images or cartoon type characters or tools

```html
<!DOCTYPE html>
<html lang="en">
<head>
<meta charset="utf-8">
<title>BuildLinkHub.com Business Card</title>
<link href="https://fonts.googleapis.com/css2?family=Catamaran:wght@400;600;700&display=swap" rel="stylesheet">
<style>
  :root {
    --page-bg: #dcd8d3;
    --card-bg: #f1f0ee;
    --ink-dark: #2f3540;
    --ink-body: #585d64;
    --accent-red: #e2452b;
  }
  * { margin: 0; padding: 0; box-sizing: border-box; }
  html, body {
    width: 1200px; height: 969px; overflow: hidden;
    background: var(--page-bg);
    font-family: "Catamaran", sans-serif;
  }
  .business-card {
    position: absolute; left: 100px; top: 200px;
    width: 1000px; height: 570px;
    background: var(--card-bg);
    box-shadow: 0 10px 30px rgba(0,0,0,0.12);
  }
  .company-name {
    position: absolute; left: 60px; top: 62px;
    display: flex; align-items: center; gap: 16px;
    font-size: 54px; font-weight: 700; line-height: 1;
    color: var(--ink-dark); letter-spacing: -0.5px;
  }
  .company-name .brand-square {
    width: 22px; height: 22px; background: var(--accent-red);
  }
  .name-marker {
    position: absolute; left: 0; top: 200px;
    width: 20px; height: 72px; background: var(--accent-red);
  }
  .person-name {
    position: absolute; left: 60px; top: 198px;
    font-size: 36px; font-weight: 600; color: var(--ink-dark); line-height: 1.1;
  }
  .person-title {
    position: absolute; left: 60px; top: 242px;
    font-size: 29px; font-weight: 400; color: var(--accent-red); line-height: 1.1;
  }
  .mailing-address {
    position: absolute; left: 60px; top: 300px;
    font-size: 26px; color: var(--ink-body); line-height: 32px; font-style: normal;
  }
  .contact-list {
    position: absolute; left: 60px; top: 378px; list-style: none;
  }
  .contact-list li {
    display: flex; align-items: center; gap: 14px;
    font-size: 26px; color: var(--ink-body); height: 38px;
  }
  .contact-list svg { width: 24px; height: 24px; fill: var(--ink-dark); flex: none; }
</style>
</head>
<body>
  <main class="business-card">
    <div class="company-name"><span class="brand-square"></span>BuildLinkHub.com</div>

    <span class="name-marker"></span>
    <h1 class="person-name">Dale Marchetti</h1>
    <p class="person-title">President</p>

    <address class="mailing-address">PO Box 947<br>Ashvale, MB, S0J2T0</address>

    <ul class="contact-list">
      <li>
        <svg viewBox="0 0 24 24" aria-hidden="true"><path d="M6.6 10.8c1.4 2.8 3.8 5.1 6.6 6.6l2.2-2.2c.3-.3.7-.4 1-.2 1.1.4 2.3.6 3.6.6.6 0 1 .4 1 1V20c0 .6-.4 1-1 1C10.6 21 3 13.4 3 4c0-.6.4-1 1-1h3.5c.6 0 1 .4 1 1 0 1.3.2 2.5.6 3.6.1.3 0 .7-.2 1l-2.3 2.2z"/></svg>
        1-800-555-0142
      </li>
      <li>
        <svg viewBox="0 0 24 24" aria-hidden="true"><path d="M7 1h10a2 2 0 0 1 2 2v18a2 2 0 0 1-2 2H7a2 2 0 0 1-2-2V3a2 2 0 0 1 2-2zm0 3v14h10V4H7zm5 15.5a1.2 1.2 0 1 0 0 2.4 1.2 1.2 0 0 0 0-2.4z"/></svg>
        306-555-0187
      </li>
      <li>
        <svg viewBox="0 0 24 24" aria-hidden="true"><path d="M2 5h20v14H2V5zm2 2v.5l8 5 8-5V7H4zm0 2.8V17h16V9.8l-8 5-8-5z"/></svg>
        dale@buildlinkhub.example
      </li>
      <li>
        <svg viewBox="0 0 24 24" aria-hidden="true"><path d="M12 2a10 10 0 1 0 0 20 10 10 0 0 0 0-20zm6.9 6h-3a15 15 0 0 0-1.3-3.9A8 8 0 0 1 18.9 8zM12 4c.8 1.2 1.5 2.5 1.9 4h-3.8c.4-1.5 1.1-2.8 1.9-4zM4.3 14a8 8 0 0 1 0-4h3.4a16 16 0 0 0 0 4H4.3zm.8 2h3a15 15 0 0 0 1.3 3.9A8 8 0 0 1 5.1 16zm3-8h-3a8 8 0 0 1 4.3-3.9C8.8 5.3 8.4 6.6 8.1 8zM12 20c-.8-1.2-1.5-2.5-1.9-4h3.8c-.4 1.5-1.1 2.8-1.9 4zm2.3-6H9.7a14 14 0 0 1 0-4h4.6a14 14 0 0 1 0 4zm.3 5.9c.6-1.2 1-2.5 1.3-3.9h3a8 8 0 0 1-4.3 3.9zm1.7-5.9a16 16 0 0 0 0-4h3.4a8 8 0 0 1 0 4h-3.4z"/></svg>
        www.buildlinkhub.example
      </li>
    </ul>
  </main>
</body>
</html>
```